Private lender of mortgages and rent to own housing

need a website that reflects real estate especially mortgage lending and rent to own houses..
Sections as follows
Home About Types of mortgages Rent to own Contact us
Target Market(s)
consumers who require non traditonal mortgages
Industry/Entity Type
Mortgage
Coding
Coded - Design and coding required
Number of Pages Required
4 page
Font styles to use
Sans Serif
Colors
Designer to choose colors to be used in the design.
Requirements
Must have
- background pictures on pages. with nice picture on homepage of houses or a community
Nice to have
- contact us form i supplied a ink to

```html
<!DOCTYPE html>
<html lang="en">
<head>
<meta charset="utf-8">
<title>Harbourline Home Lending – Rent to Own a Home</title>
<link rel="stylesheet" href="https://fonts.googleapis.com/css2?family=Didact+Gothic&family=Montserrat:wght@800&family=Questrial&display=swap">
<style>
:root{
  --navy:#27215f;
  --navy-deep:#1d1850;
  --ink:#333333;
  --muted:#555555;
  --paper:#ffffff;
  --soft:#f5f5f5;
  --rule:#4a4488;
  --footer-text:#d9d7ee;
}
*{box-sizing:border-box;margin:0;padding:0}
html,body{width:734px;height:1200px;overflow:hidden;background:var(--paper)}
body{position:relative;font-family:"Didact Gothic",sans-serif;color:var(--ink)}
h1,h2,h3{font-weight:400}
.abs{position:absolute}

/* header */
.site-header{left:0;top:0;width:734px;height:68px;background:var(--paper)}
.brand{left:60px;top:27px;display:flex;align-items:center;gap:8px;font-family:"Questrial",sans-serif;font-weight:400;font-size:14px;color:var(--navy)}
.brand-mark{width:10px;height:10px;background:var(--navy);border-radius:50%}
.main-nav{right:60px;top:33px;display:flex;gap:23px;font-family:"Questrial",sans-serif;font-size:8.6px;color:var(--ink);text-transform:uppercase}
.main-nav a{color:inherit;text-decoration:none;position:relative}
.main-nav a.active{color:var(--navy)}
.main-nav a.active::after{content:"";position:absolute;left:-2px;right:-2px;top:13px;height:1.5px;background:var(--navy)}

/* hero */
.hero{left:0;top:68px;width:734px;height:400px;background:linear-gradient(100deg,#6f6a60 0%,#a08d78 30%,#c8bfae 55%,#e3e0d8 75%,#9aa0a0 100%)}
.hero-curve{left:0;top:380px;width:734px;height:90px}
.hero-title{left:0;top:206px;width:734px;text-align:center;font-family:"Montserrat",sans-serif;font-weight:800;font-size:46px;color:#fff;letter-spacing:1px;line-height:1}
.hero-sub{left:0;top:255px;width:734px;text-align:center;font-family:"Questrial",sans-serif;font-size:13px;color:#fff}
.hero-arrow{top:238px;width:20px;height:26px}

/* welcome */
.welcome-title{left:0;top:478px;width:734px;text-align:center;font-family:"Questrial",sans-serif;font-size:23px;color:var(--ink)}
.welcome-copy{left:76px;width:582px;text-align:center;font-size:8.3px;line-height:16.3px;color:var(--muted)}

/* services */
.services{left:0;top:674px;width:734px;height:316px;background:var(--soft)}
.services-title{left:0;top:36px;width:734px;text-align:center;font-family:"Questrial",sans-serif;font-size:21px;color:var(--ink)}
.service{top:92px;width:140px;text-align:center}
.service-icon{display:block;margin:0 auto;width:78px;height:78px}
.service-name{margin-top:8px;font-family:"Questrial",sans-serif;font-size:11px;color:var(--ink);letter-spacing:.3px}
.service-text{margin-top:6px;padding:0 6px;font-size:6.8px;line-height:12px;color:var(--muted);height:36px}
.read-more{display:inline-block;margin-top:9px;width:79px;height:23px;line-height:21px;border:1px solid var(--navy);font-family:"Questrial",sans-serif;font-size:8.6px;color:var(--navy);text-decoration:none;background:var(--paper)}

/* footer */
.site-footer{left:0;top:990px;width:734px;height:210px;background:var(--navy)}
.footer-heading{top:33px;font-family:"Questrial",sans-serif;font-size:11px;color:#fff;letter-spacing:.3px}
.footer-links{top:53px;list-style:none;font-size:8.6px;line-height:19.4px;color:var(--footer-text)}
.footer-divider{top:28px;width:1px;height:120px;background:var(--rule)}
.contact-list{left:297px;top:54px;list-style:none;font-size:8.6px;line-height:16px;color:var(--footer-text)}
.contact-list li{display:flex;align-items:center;gap:9px}
.contact-list svg{width:9px;height:9px}
.news-text{left:473px;top:53px;font-size:8.6px;color:var(--footer-text)}
.news-form{left:474px;top:69px;display:flex}
.news-input{width:136px;height:23px;border:0;background:#fff;padding-left:9px;font-family:"Didact Gothic",sans-serif;font-size:8.5px;color:#aaa;line-height:23px}
.news-button{width:64px;height:23px;background:var(--navy-deep);color:#fff;font-family:"Questrial",sans-serif;font-size:8.8px;text-align:center;line-height:23px}
.social{left:474px;top:101px;display:flex;gap:6px}
.social span{width:24px;height:24px;border-radius:50%;background:#fff}
.footer-rule{left:60px;top:166px;width:614px;height:1px;background:#6a64a6}
.copyright{left:60px;top:179px;font-size:8.6px;color:var(--footer-text)}
</style>
</head>
<body>

<header class="abs site-header">
  <div class="abs brand"><span class="brand-mark"></span>Harbourline Home Lending</div>
  <nav class="abs main-nav">
    <a class="active" href="#">Home</a>
    <a href="#">About</a>
    <a href="#">Types of Mortgages</a>
    <a href="#">Rent to Own</a>
    <a href="#">Contact Us</a>
  </nav>
</header>

<div class="abs hero" role="img" aria-label="Photo of a smiling couple holding house keys in front of their new home"></div>
<svg class="abs hero-curve" viewBox="0 0 734 90" preserveAspectRatio="none" aria-hidden="true">
  <path d="M0 84 Q367 0 734 84 L734 90 L0 90 Z" fill="#ffffff"/>
</svg>
<h1 class="abs hero-title">RENT TO OWN A HOME</h1>
<p class="abs hero-sub">We provide mortgage lending and rent to own houses.</p>
<svg class="abs hero-arrow" style="left:16px" viewBox="0 0 20 26" aria-hidden="true"><path d="M13 4 L6 13 L13 22" stroke="#fff" stroke-width="1.2" fill="none" opacity=".8"/></svg>
<svg class="abs hero-arrow" style="left:698px" viewBox="0 0 20 26" aria-hidden="true"><path d="M7 4 L14 13 L7 22" stroke="#fff" stroke-width="1.2" fill="none" opacity=".8"/></svg>

<h2 class="abs welcome-title">Welcome to Harbourline Home Lending</h2>
<p class="abs welcome-copy" style="top:513px">We know life sometimes delivers challenges and it can be hard to get back on track once you have dealt with challenges. Maybe you have been through a divorce, bankruptcy, consumer propospal, loss of job, work place injury, new to the country, self-employed or some credit related challenges that have you behind the eight ball? Are these challenges making it difficult to get a mortgage?</p>
<p class="abs welcome-copy" style="top:576px">None of these things has to bind you to a lifetime of renting. Want to start paying yourself first? We focus on rent to own in Lakeshore County and our Renting Program is a very viable option for those that can't get a mortgage today but are willing to work towards getting approved in the near future while living in their own home that they select. Homeownership is closer than you think.</p>

<section class="abs services">
  <h2 class="abs services-title">Our Services</h2>

  <div class="abs service" style="left:55px">
    <svg class="service-icon" viewBox="0 0 80 80" aria-hidden="true">
      <circle cx="40" cy="40" r="39" fill="#fff"/><circle cx="40" cy="40" r="36" fill="var(--navy)"/>
      <g stroke="#fff" stroke-width="2" fill="none"><rect x="27" y="32" width="24" height="14" transform="rotate(-25 39 39)"/><circle cx="39" cy="39" r="3"/><path d="M44 50 l6 -6 M47 50 h4 v-4"/></g>
    </svg>
    <div class="service-name">DOWN PAYMENT</div>
    <p class="service-text">We require a minimum down payment of $10,000 or 3.5% to 4% of total price of the home (whichever is larger).</p>
    <a class="read-more" href="#">READ MORE</a>
  </div>

  <div class="abs service" style="left:216px">
    <svg class="service-icon" viewBox="0 0 80 80" aria-hidden="true">
      <circle cx="40" cy="40" r="39" fill="#fff"/><circle cx="40" cy="40" r="36" fill="var(--navy)"/>
      <g stroke="#fff" stroke-width="2" fill="none"><rect x="31" y="30" width="24" height="16" rx="2"/><path d="M31 35 h24"/><path d="M22 48 h10 l6 -4 h6"/></g>
    </svg>
    <div class="service-name">HOUSEHOLD INCOME</div>
    <p class="service-text">Steady, provable household income that can support the price of the home you would like.</p>
    <a class="read-more" href="#">READ MORE</a>
  </div>

  <div class="abs service" style="left:378px">
    <svg class="service-icon" viewBox="0 0 80 80" aria-hidden="true">
      <circle cx="40" cy="40" r="39" fill="#fff"/><circle cx="40" cy="40" r="36" fill="var(--navy)"/>
      <g stroke="#fff" stroke-width="2" fill="none"><rect x="30" y="28" width="18" height="24" rx="1"/><rect x="35" y="25" width="8" height="5"/><path d="M34 36 h10 M34 41 h10 M34 46 h6"/></g>
      <circle cx="48" cy="49" r="5" fill="#fff"/><path d="M45.5 49 l2 2 l3.5 -4" stroke="var(--navy)" stroke-width="1.5" fill="none"/>
    </svg>
    <div class="service-name">CREDIT REPORT</div>
    <p class="service-text">We require a minimum down payment of $10,000 or 3.5% to 4% of total price of the home (whichever is larger).</p>
    <a class="read-more" href="#">READ MORE</a>
  </div>

  <div class="abs service" style="left:539px">
    <svg class="service-icon" viewBox="0 0 80 80" aria-hidden="true">
      <circle cx="40" cy="40" r="39" fill="#fff"/><circle cx="40" cy="40" r="36" fill="var(--navy)"/>
      <g stroke="#fff" stroke-width="2" fill="none"><path d="M26 40 L40 27 L54 40"/><path d="M30 37 v15 h20 v-15"/><rect x="37" y="43" width="6" height="9"/><rect x="33" y="40" width="3" height="3"/></g>
    </svg>
    <div class="service-name">SELECTING A HOUSE</div>
    <p class="service-text">We require a minimum down payment of $10,000 or 3.5% to 4% of total price of the home (whichever is larger).</p>
    <a class="read-more" href="#">READ MORE</a>
  </div>
</section>

<footer class="abs site-footer">
  <h3 class="abs footer-heading" style="left:60px">QUICK LINKS</h3>
  <ul class="abs footer-links" style="left:60px"><li>Home</li><li>About</li><li>Types of mortgages</li><li>Rent to own</li></ul>
  <ul class="abs footer-links" style="left:171px"><li>Terms of Service</li><li>Privacy Policy</li><li>Contact Us</li></ul>
  <div class="abs footer-divider" style="left:260px"></div>

  <h3 class="abs footer-heading" style="left:297px">CONTACT INFO</h3>
  <ul class="contact-list abs">
    <li>Harbourline Home Lending ,</li>
    <li>Pinecrest, Ontario</li>
    <li style="margin-top:3px"><svg viewBox="0 0 10 10" aria-hidden="true"><rect width="10" height="10" rx="1.5" fill="#fff"/><path d="M3 2.5 q-1 2.5 1.5 5 l1-1 l1.5 1" stroke="var(--navy)" stroke-width="1.2" fill="none"/></svg>+00 555 01 23 456</li>
    <li style="margin-top:3px"><svg viewBox="0 0 10 10" aria-hidden="true"><rect y="1.5" width="10" height="7" fill="#fff"/><path d="M0 1.5 L5 5.5 L10 1.5" stroke="var(--navy)" stroke-width="1" fill="none"/></svg>hello@harbourlinehome.ca</li>
  </ul>
  <div class="abs footer-divider" style="left:445px"></div>

  <h3 class="abs footer-heading" style="left:473px">SIGN UP FOR NEWSLETTERS</h3>
  <p class="abs news-text">Please sign up here for latest news</p>
  <div class="abs news-form"><div class="news-input">EMAIL ADDRESS</div><div class="news-button">SUBSCRIBE</div></div>
  <div class="abs social" aria-label="Social links"><span></span><span></span><span></span><span></span></div>

  <div class="abs footer-rule"></div>
  <p class="abs copyright">© 2017 HARBOURLINE HOME LENDING.&nbsp; All right reserved . Term of Use</p>
</footer>

</body>
</html>
```